Paperwell Solutions Services Flyer

Create a 2 sided A4 flyer/PDF of the services we offer and a description of each etc.
Details can be found at: https://www.paperwell-solutions.co.uk/
Main services: Document Scanning, Invoice Processing and other services we offer.

Industry/Entity Type

Document Management

Font styles to use
Other font styles liked:
• Montserrat

Colors

Designer to choose colors to be used in the design.

Requirements
Must have
• Document Scanning, Box Storage, Invoice Processing, Book Scanning, Large format scanning
Nice to have
• Colourful d/s flyer listing our services with a brief description on each

```html
<!DOCTYPE html>
<html lang="en">
<head>
<meta charset="utf-8">
<title>Paperwell Solutions – Services Flyer</title>
<link rel="stylesheet" href="https://fonts.googleapis.com/css2?family=Montserrat:wght@400;500;600;700;800&display=swap">
<style>
  :root{
    --teal:#1f9bab;
    --teal-dark:#16697c;
    --navy:#173b55;
    --ink:#1c3550;
    --red:#d3252b;
    --pink:#c04aa8;
    --night:#231f4a;
    --paper:#f4f6f8;
    --bg:#e4e6e9;
  }
  *{box-sizing:border-box;margin:0;padding:0}
  html,body{width:1200px;height:848px;overflow:hidden;background:var(--bg);font-family:"Montserrat",sans-serif}
  .canvas{position:relative;width:1200px;height:848px}
  .page{position:absolute;top:44px;width:537px;height:760px;background:var(--paper);overflow:hidden;box-shadow:0 4px 18px rgba(0,0,0,.18)}
  .page--front{left:43px}
  .page--back{left:620px}

  /* shared */
  .hero{position:absolute;left:0;top:0;width:100%;background:linear-gradient(135deg,#1d2a5a 0%,#2c3f77 35%,#7a3c8f 60%,#1e4f6e 100%)}
  .hero__shade{position:absolute;inset:0;background:linear-gradient(180deg,rgba(20,22,50,.35),rgba(20,22,50,.65))}
  .site-vertical{position:absolute;writing-mode:vertical-rl;font-size:9px;letter-spacing:5px;color:var(--ink)}

  /* front */
  .front-hero{height:250px}
  .brand-name{position:absolute;left:0;right:0;top:40px;display:flex;justify-content:center;align-items:center;gap:8px;color:#fff;font-weight:600;font-size:18px;line-height:1}
  .brand-name__square{width:10px;height:10px;background:#fff}
  .front-title{position:absolute;left:0;right:0;top:104px;text-align:center;color:#fff;font-weight:700;font-size:25px}
  .contact-btn{position:absolute;left:50%;top:146px;transform:translateX(-50%);border:1.5px solid #fff;border-radius:4px;padding:4px 12px;color:#fff;font-size:10px;font-weight:600;letter-spacing:.5px}
  .hex-grid{position:absolute;left:0;top:250px}
  .hex-label{font-family:"Montserrat",sans-serif;font-weight:700;fill:#fff;font-size:14px;text-anchor:middle}
  .hex-brand{font-family:"Montserrat",sans-serif;font-weight:600;fill:#fff;font-size:15px;text-anchor:middle}
  .footer{position:absolute;left:0;bottom:0;width:100%;height:140px}
  .footer__content{position:absolute;left:0;bottom:0;width:100%;height:100px;display:flex;justify-content:space-between;align-items:flex-start;padding:26px 40px 0;color:#fff;font-size:9px;line-height:1.35}
  .contact-line{display:flex;align-items:center;gap:6px;margin-bottom:4px}
  .contact-line svg{width:10px;height:10px;fill:#fff}
  .address{display:flex;gap:6px}
  .certs{text-align:center}
  .certs__badges{display:flex;gap:8px;justify-content:center;margin-bottom:6px}
  .badge-circle{width:22px;height:22px;border-radius:50%;border:2px solid #fff}
  .badge-square{width:22px;height:22px;border:2px solid #fff;border-radius:3px}
  .badge-wide{width:32px;height:22px;background:rgba(255,255,255,.85);border-radius:3px}
  .certs strong{font-weight:700;display:block}

  /* back */
  .back-hero{height:205px;background:linear-gradient(135deg,#1b2450 0%,#26305e 45%,#4a2f6e 75%,#1b3f5e 100%)}
  .back-title{position:absolute;left:0;right:0;top:28px;text-align:center;color:#fff;font-weight:700;font-size:24px}
  .back-intro{position:absolute;left:50px;right:50px;top:70px;text-align:center;color:#fff;font-size:10.5px;line-height:1.45}
  .service-group{position:absolute;left:42px;width:455px;border:1.5px solid var(--teal-dark);border-radius:12px;padding:9px 18px 4px}
  .service{display:flex;gap:12px;margin-bottom:7px}
  .service__icon{flex:0 0 30px;height:30px}
  .service__title{font-weight:700;font-size:14px;color:var(--navy);margin-bottom:2px}
  .service__text{font-size:7.5px;line-height:1.35;color:#3b4c5e}
</style>
</head>
<body>
<div class="canvas">

  <!-- FRONT SIDE -->
  <section class="page page--front">
    <div class="hero front-hero" role="img" aria-label="Photo of a document archive room with shelves of files and a scanner lit in blue and pink">
      <div class="hero__shade"></div>
    </div>
    <div class="brand-name"><span class="brand-name__square"></span>Paperwell Solutions</div>
    <h1 class="front-title">Document Automation Services</h1>
    <div class="contact-btn">CONTACT US</div>

    <svg class="hero-band" style="position:absolute;left:0;top:200px" width="537" height="80" viewBox="0 0 537 80">
      <polygon points="0,28 537,28 537,80 0,56" fill="var(--teal)"/>
      <rect x="0" y="20" width="90" height="14" fill="var(--teal)"/>
      <rect x="340" y="22" width="120" height="12" fill="var(--teal)"/>
      <rect x="140" y="36" width="190" height="10" fill="var(--red)"/>
      <rect x="20" y="40" width="110" height="10" fill="var(--teal-dark)"/>
      <rect x="360" y="40" width="90" height="10" fill="var(--teal-dark)"/>
      <rect x="30" y="8" width="8" height="8" fill="var(--teal)"/>
      <rect x="440" y="60" width="8" height="8" fill="var(--teal-dark)"/>
      <rect x="110" y="62" width="6" height="6" fill="var(--teal)"/>
    </svg>

    <svg class="hex-grid" width="537" height="400" viewBox="0 0 537 400">
      <defs>
        <linearGradient id="photoBlue" x1="0" y1="0" x2="1" y2="1">
          <stop offset="0" stop-color="#2a3d7a"/><stop offset="1" stop-color="#1a5a78"/>
        </linearGradient>
        <linearGradient id="photoPink" x1="0" y1="0" x2="1" y2="1">
          <stop offset="0" stop-color="#c14aa4"/><stop offset="1" stop-color="#2e2e60"/>
        </linearGradient>
        <linearGradient id="photoGrey" x1="0" y1="0" x2="1" y2="1">
          <stop offset="0" stop-color="#6e8296"/><stop offset="1" stop-color="#2b3b52"/>
        </linearGradient>
        <polygon id="hexFrame" points="0,-74 64,-37 64,37 0,74 -64,37 -64,-37"/>
        <polygon id="hexPhoto" points="0,-66 57,-33 57,33 0,66 -57,33 -57,-33"/>
      </defs>

      <rect x="40" y="30" width="80" height="50" rx="4" fill="#8d9aa8" role="img" aria-label="Large format scanner"/>
      <rect x="32" y="82" width="92" height="8" fill="var(--teal)"/>
      <rect x="420" y="78" width="76" height="48" rx="4" fill="#9aa6b2" role="img" aria-label="Desktop document scanner"/>
      <rect x="410" y="128" width="90" height="8" fill="var(--teal)"/>
      <rect x="40" y="256" width="62" height="60" rx="4" fill="#8693a2" role="img" aria-label="Overhead book scanner"/>
      <rect x="30" y="318" width="86" height="8" fill="var(--teal)"/>
      <rect x="422" y="318" width="72" height="40" rx="4" fill="#9aa6b2" role="img" aria-label="Production document scanner"/>
      <rect x="410" y="360" width="90" height="8" fill="var(--teal)"/>

      <g transform="translate(204,80)">
        <use href="#hexFrame" fill="#fff" stroke="var(--teal)" stroke-width="2"/>
        <use href="#hexPhoto" fill="url(#photoBlue)" role="img" aria-label="Scanning workstation photo"/>
        <text class="hex-label" y="22">Document</text><text class="hex-label" y="38">Scanning</text>
      </g>
      <g transform="translate(332,80)">
        <use href="#hexFrame" fill="#fff" stroke="var(--teal)" stroke-width="2"/>
        <use href="#hexPhoto" fill="url(#photoPink)" role="img" aria-label="Archive boxes on shelves photo"/>
        <text class="hex-label" y="22">Box</text><text class="hex-label" y="38">Storage</text>
      </g>
      <g transform="translate(140,191)">
        <use href="#hexFrame" fill="#fff" stroke="var(--teal)" stroke-width="2"/>
        <use href="#hexPhoto" fill="url(#photoPink)" role="img" aria-label="Invoice passing through a scanner photo"/>
        <text class="hex-label" y="22">Invoice</text><text class="hex-label" y="38">Processing</text>
      </g>
      <g transform="translate(268,191)">
        <use href="#hexPhoto" fill="var(--teal)" transform="scale(1.1)"/>
        <text class="hex-brand" y="-3">Paperwell</text><text class="hex-brand" y="16">Solutions</text>
      </g>
      <g transform="translate(396,191)">
        <use href="#hexFrame" fill="#fff" stroke="var(--teal)" stroke-width="2"/>
        <use href="#hexPhoto" fill="url(#photoGrey)" role="img" aria-label="Book scanning machine photo"/>
        <text class="hex-label" y="22">Book</text><text class="hex-label" y="38">Scanning</text>
      </g>
      <g transform="translate(204,302)">
        <use href="#hexFrame" fill="#fff" stroke="var(--teal)" stroke-width="2"/>
        <use href="#hexPhoto" fill="url(#photoGrey)" role="img" aria-label="Large format scanner photo"/>
        <text class="hex-label" y="14">Large Format</text><text class="hex-label" y="30">Scanning</text>
      </g>
      <g transform="translate(332,302)">
        <use href="#hexFrame" fill="#fff" stroke="var(--teal)" stroke-width="2"/>
        <use href="#hexPhoto" fill="url(#photoBlue)" role="img" aria-label="Data centre corridor photo"/>
        <text class="hex-label" y="4">Our Services</text><text class="hex-label" y="20">More Than</text><text class="hex-label" y="36">This...</text>
      </g>
    </svg>

    <div class="site-vertical" style="left:12px;top:300px">paperwell-solutions.co.uk</div>
    <div class="site-vertical" style="right:10px;top:360px">paperwell-solutions.co.uk</div>

    <svg class="footer" width="537" height="140" viewBox="0 0 537 140" preserveAspectRatio="none">
      <path d="M0,30 Q140,0 270,30 T537,30 L537,140 L0,140 Z" fill="var(--teal-dark)"/>
      <path d="M0,40 Q140,14 270,42 T537,44 L537,52 Q400,56 270,52 T0,50 Z" fill="var(--teal)"/>
    </svg>
    <div class="footer__content">
      <div>
        <div class="contact-line"><svg viewBox="0 0 24 24"><path d="M6.6 10.8a15 15 0 0 0 6.6 6.6l2.2-2.2a1 1 0 0 1 1-.25 11.4 11.4 0 0 0 3.6.57 1 1 0 0 1 1 1V20a1 1 0 0 1-1 1A17 17 0 0 1 3 4a1 1 0 0 1 1-1h3.5a1 1 0 0 1 1 1c0 1.25.2 2.45.57 3.57a1 1 0 0 1-.25 1z"/></svg>01632 960418</div>
        <div class="contact-line"><svg viewBox="0 0 24 24"><path d="M2 5h20v14H2z M2 5l10 8 10-8" fill="none" stroke="#fff" stroke-width="2"/></svg>sales@paperwell.co.uk</div>
      </div>
      <div class="address">
        <svg width="10" height="12" viewBox="0 0 24 30"><path d="M12 0a10 10 0 0 0-10 10c0 8 10 20 10 20s10-12 10-20A10 10 0 0 0 12 0zm0 14a4 4 0 1 1 0-8 4 4 0 0 1 0 8z" fill="#fff"/></svg>
        <div>Alder Court,<br>Millbank Road<br>Hartfield, East<br>Sussex<br>TN7 4QD</div>
      </div>
      <div class="certs">
        <div class="certs__badges"><span class="badge-circle"></span><span class="badge-square"></span><span class="badge-wide"></span></div>
        <strong>Certificate No. 20482</strong>ISO 9001 ISO 27001
      </div>
    </div>
  </section>

  <!-- BACK SIDE -->
  <section class="page page--back">
    <div class="hero back-hero" role="img" aria-label="Dark photo of an office archive with stacked paper files">
      <div class="hero__shade"></div>
    </div>
    <h2 class="back-title">Document Automation Services</h2>
    <p class="back-intro">At Paperwell Solutions, we deliver award-winning document automation services, from business process optimization and document management to data capture and document scanning.<br>We specialize in transforming your most labour-intensive workflows into cost-effective automated solutions, helping you save money, enhance efficiency, and grow your business.</p>

    <svg style="position:absolute;left:14px;top:215px" width="24" height="50" viewBox="0 0 24 50">
      <rect x="0" y="0" width="10" height="10" fill="var(--navy)"/><rect x="10" y="10" width="10" height="10" fill="var(--navy)"/>
      <rect x="0" y="20" width="10" height="10" fill="var(--navy)"/><rect x="10" y="34" width="6" height="6" fill="var(--teal)"/>
    </svg>

    <div class="site-vertical" style="left:12px;top:300px">paperwell-solutions.co.uk</div>
    <div class="site-vertical" style="right:10px;top:360px">paperwell-solutions.co.uk</div>

    <div class="service-group" style="top:216px">
      <div class="service">
        <svg class="service__icon" viewBox="0 0 30 30"><rect x="7" y="3" width="18" height="24" rx="2" fill="var(--navy)"/><rect x="4" y="6" width="18" height="22" rx="2" fill="none" stroke="var(--navy)" stroke-width="1.5"/><circle cx="6" cy="8" r="3" fill="var(--red)"/></svg>
        <div><h3 class="service__title">Document Scanning</h3><p class="service__text">Digitise your physical files with our high-volume scanning services, turning paper records into searchable PDF files that are easy to find and share.</p></div>
      </div>
      <div class="service">
        <svg class="service__icon" viewBox="0 0 30 30"><rect x="3" y="5" width="18" height="22" rx="2" fill="var(--navy)"/><circle cx="23" cy="12" r="5" fill="none" stroke="var(--red)" stroke-width="2"/></svg>
        <div><h3 class="service__title">Document Processing</h3><p class="service__text">Streamline operations with tailored processing systems that replace manual workflows, reduce human error and cut the cost of paper-based tasks.</p></div>
      </div>
      <div class="service">
        <svg class="service__icon" viewBox="0 0 30 30"><rect x="4" y="12" width="22" height="15" rx="2" fill="#8c96a3"/><rect x="8" y="3" width="14" height="10" fill="var(--navy)"/><rect x="12" y="17" width="6" height="3" fill="#fff"/></svg>
        <div><h3 class="service__title">Box Storage</h3><p class="service__text">Secure your critical records in our monitored storage facilities, with reliable retrieval of both physical boxes and digital files when needed.</p></div>
      </div>
    </div>

    <div class="service-group" style="top:380px">
      <div class="service">
        <svg class="service__icon" viewBox="0 0 30 30"><circle cx="9" cy="18" r="6" fill="none" stroke="var(--red)" stroke-width="2.5"/><circle cx="21" cy="18" r="6" fill="none" stroke="var(--navy)" stroke-width="2.5"/><circle cx="15" cy="8" r="5" fill="none" stroke="var(--teal-dark)" stroke-width="2.5"/></svg>
        <div><h3 class="service__title">Secure Document Destruction</h3><p class="service__text">Dispose of obsolete or sensitive documents safely with our certified destruction service, meeting strict regulatory requirements every time.</p></div>
      </div>
      <div class="service">
        <svg class="service__icon" viewBox="0 0 30 30"><path d="M3 10h10l3 3h11v14H3z" fill="var(--teal-dark)"/><rect x="16" y="3" width="10" height="12" fill="var(--red)"/></svg>
        <div><h3 class="service__title">Document Management Systems</h3><p class="service__text">Centralise your information in one searchable repository, bringing documents together for better access, collaboration and day-to-day productivity.</p></div>
      </div>
      <div class="service">
        <svg class="service__icon" viewBox="0 0 30 30"><rect x="3" y="7" width="20" height="14" rx="2" fill="none" stroke="var(--navy)" stroke-width="2"/><circle cx="9" cy="14" r="2.5" fill="var(--red)"/><path d="M22 14h6M25 11l3 3-3 3" stroke="var(--red)" stroke-width="1.8" fill="none"/></svg>
        <div><h3 class="service__title">Digital Mailroom</h3><p class="service__text">Future-proof your business by digitising incoming post and routing it automatically, replacing slow paper-based processes with modern systems.</p></div>
      </div>
    </div>

    <div class="service-group" style="top:544px">
      <div class="service">
        <svg class="service__icon" viewBox="0 0 30 30"><circle cx="22" cy="12" r="6" fill="var(--navy)"/><path d="M3 22l14-8" stroke="var(--navy)" stroke-width="4"/></svg>
        <div><h3 class="service__title">Microfilm Digitisation</h3><p class="service__text">Preserve historical data by converting microfilm records into searchable, high-quality digital formats that protect your archives for years.</p></div>
      </div>
      <div class="service">
        <svg class="service__icon" viewBox="0 0 30 30"><circle cx="11" cy="16" r="7" fill="none" stroke="var(--navy)" stroke-width="3"/><circle cx="22" cy="10" r="5" fill="none" stroke="var(--teal-dark)" stroke-width="2.5"/><circle cx="11" cy="16" r="2" fill="var(--red)"/></svg>
        <div><h3 class="service__title">Workflow Systems</h3><p class="service__text">Transform your operations with tailored workflow systems that automate tasks, reduce manual steps and keep information flowing across teams.</p></div>
      </div>
      <div class="service">
        <svg class="service__icon" viewBox="0 0 30 30"><rect x="8" y="5" width="14" height="20" rx="1" fill="var(--navy)"/><path d="M3 3h4M3 3v4M27 3h-4M27 3v4M3 27h4M3 27v-4M27 27h-4M27 27v-4" stroke="var(--red)" stroke-width="1.8"/></svg>
        <div><h3 class="service__title">Large Format Scanning</h3><p class="service__text">Our specialised service digitises oversized materials such as plans, maps and posters with precision, so no detail is lost.</p></div>
      </div>
    </div>

    <svg style="position:absolute;left:0;bottom:0" width="537" height="44" viewBox="0 0 537 44">
      <rect x="0" y="8" width="90" height="10" fill="var(--teal)"/>
      <rect x="0" y="18" width="300" height="10" fill="var(--teal-dark)"/>
      <rect x="80" y="24" width="100" height="8" fill="var(--red)"/>
      <rect x="190" y="26" width="110" height="14" fill="var(--navy)"/>
      <rect x="490" y="4" width="10" height="10" fill="var(--navy)"/><rect x="500" y="14" width="10" height="10" fill="var(--navy)"/>
      <rect x="470" y="32" width="7" height="7" fill="var(--teal)"/>
    </svg>
  </section>

</div>
</body>
</html>
```